Yearbook of one of our programs

Our company, Bluewater Circle, www.bluewatercircle.example, hosts leadership programs and workshops for women in leadership roles from different companies all around the world. We need a year book, 11 x 17 inches, we will print with a soft cover, and be approximately 70 pages. Due date for the final completion is 12/9. However, the initial contest & fee is only for pages 1-5, 26-27 and 40-41 (please see attached last year's version). We’d like to use the same color as that. Also attached is the outline we will use once a designer is selected. $50 hourly rate for the completion of the book is set once a designer is confirmed.

```html
<!DOCTYPE html>
<html lang="en">
<head>
<meta charset="utf-8">
<title>Bluewater Circle Yearbook – Pages 02–03</title>
<link href="https://fonts.googleapis.com/css2?family=Open+Sans:wght@300;400;600&family=Satisfy&display=swap" rel="stylesheet">
<style>
  :root {
    --crimson: #b22b5c;
    --crimson-deep: #8f1f45;
    --ink: #2f3140;
    --body: #585b68;
    --slate: #4a4d5c;
    --paper: #ffffff;
    --paper-cool: #eef0f5;
    --paper-grey: #d9dce4;
    --backdrop: #2a2624;
  }
  * { box-sizing: border-box; margin: 0; padding: 0; }
  html, body {
    width: 1200px; height: 789px; overflow: hidden;
    background: var(--backdrop);
    font-family: "Open Sans", Arial, sans-serif;
  }
  .spread {
    position: absolute; left: 100px; top: 44px;
    width: 1000px; height: 700px;
    display: flex;
    box-shadow: 0 18px 40px rgba(0,0,0,.45);
  }
  .page { position: relative; width: 500px; height: 700px; overflow: hidden; }
  .page-left { background: var(--crimson); }
  .page-right { background: linear-gradient(90deg, #e9ebf1 0%, var(--paper) 8%, var(--paper) 100%); }
  .page-art { position: absolute; inset: 0; width: 100%; height: 100%; }

  .photo-frame {
    position: absolute; left: 58px; top: 42px; width: 364px; height: 478px;
    border: 2px solid var(--paper); padding: 7px;
  }
  .photo {
    width: 100%; height: 100%;
    background: linear-gradient(160deg, #d9d3c8 0%, #b8c4cf 30%, #8a6f55 55%, #3c3533 80%, #2b2a2e 100%);
  }

  .footer-band {
    position: absolute; left: 0; top: 610px; height: 22px; width: 232px;
    background: var(--crimson);
    clip-path: polygon(0 0, 100% 0, 94% 100%, 0 100%);
    display: flex; align-items: center; gap: 7px; padding-left: 22px;
    color: var(--paper); font-size: 11px; font-weight: 300; letter-spacing: .2px;
    white-space: nowrap;
  }
  .footer-band .dot { width: 8px; height: 8px; border-radius: 50%; background: var(--paper); }
  .footer-rule {
    position: absolute; left: 238px; top: 628px; right: 0; height: 3px; background: var(--slate);
  }
  .folio {
    position: absolute; right: 34px; top: 646px;
    font-size: 11px; letter-spacing: .6px; color: var(--crimson); text-transform: uppercase;
    white-space: nowrap;
  }
  .folio .num { color: var(--ink); margin-left: 6px; padding-left: 7px; border-left: 1px solid var(--crimson); }

  .title-band {
    position: absolute; left: 0; top: 32px; width: 250px; height: 38px;
    background: var(--crimson);
    clip-path: polygon(0 0, 100% 0, 93% 100%, 0 100%);
    color: var(--paper); font-family: "Satisfy", "Brush Script MT", cursive; font-size: 22px;
    display: flex; align-items: center; padding-left: 22px; white-space: nowrap;
  }
  .title-slash {
    position: absolute; left: 250px; top: 36px; width: 4px; height: 34px;
    background: var(--slate); transform: skewX(-28deg);
  }
  .floral {
    position: absolute; right: 10px; top: 70px; width: 120px; height: 160px;
    background: radial-gradient(ellipse at center, rgba(201,70,118,.12) 0%, rgba(201,70,118,0) 70%);
  }
  .letter {
    position: absolute; left: 44px; top: 96px; width: 410px;
    font-size: 10.6px; line-height: 1.5; color: var(--body); font-weight: 300;
  }
  .letter p { margin-bottom: 12px; }
  .salutation { color: var(--ink); font-weight: 400; font-size: 12px; }
  .lead { color: var(--ink); font-weight: 600; font-size: 11.4px; }
  .pull-quote {
    position: absolute; left: 0; top: 390px; width: 420px; height: 22px;
    background: var(--crimson);
    clip-path: polygon(0 0, 100% 0, 96% 100%, 0 100%);
    color: var(--paper); font-size: 10.4px; font-weight: 400;
    display: flex; align-items: center; padding-left: 44px; white-space: nowrap;
  }
  .closing { top: 424px; }
  .sign-off {
    position: absolute; left: 44px; top: 540px;
    font-size: 12px; color: var(--ink);
  }
  .signature {
    position: absolute; left: 44px; top: 562px; width: 120px; height: 36px;
    background: linear-gradient(90deg, rgba(47,49,64,.18), rgba(47,49,64,.05));
    border-radius: 4px;
  }
</style>
</head>
<body>
<main class="spread">
  <section class="page page-left">
    <svg class="page-art" viewBox="0 0 500 700" aria-hidden="true">
      <path d="M0 480 Q 330 480 500 570 L500 600 Q 330 500 0 500 Z" fill="var(--crimson-deep)"/>
      <path d="M0 500 Q 330 500 500 600 L500 700 L0 700 Z" fill="var(--paper-grey)"/>
      <path d="M0 514 Q 320 514 500 616 L500 700 L0 700 Z" fill="var(--paper-cool)"/>
    </svg>
    <div class="photo-frame">
      <div class="photo" role="img" aria-label="Photo of program members chatting and laughing outdoors on a sunny deck"></div>
    </div>
    <div class="footer-band"><span class="dot"></span>www.bluewatercircle.example</div>
    <div class="footer-rule"></div>
    <div class="folio">Summit Rise<span class="num">02</span></div>
  </section>

  <section class="page page-right">
    <div class="title-band">A Heartfelt Thankyou</div>
    <div class="title-slash"></div>
    <div class="floral" role="img" aria-label="Faint floral line drawing"></div>

    <div class="letter">
      <p class="salutation">Ladies,</p>
      <p class="lead">What a year it has been! We put 2020 in our rearview, yet many of the challenges followed us. Despite the continued conditions 2021 presented, we faced them together, and stand stronger and wiser as a result.</p>
      <p>This year, we were able to be back in person with two magnificent Summit Rise gatherings, in Park City, Utah and “down at the farm” near Atlanta, Georgia. And throughout the year, we maintained constant connection through our virtual sessions, small group huddles, and one-on-one connections, which I’ve become quite fond of as well.</p>
      <p>When we gathered in Utah, I opened the session asking us all to think how much “Words Matter.” More than ever, a single expression of support, an open query for help, a small note to share how we are thinking of each other, or suggestions for the “must-have” beauty products… these have helped fuel us along this often rocky, unstable journey.</p>
    </div>

    <div class="pull-quote">But the word I offered in Utah to put in front of us was “remarkable.”</div>

    <div class="letter closing">
      <p>While 2021 has been remarkable in so many ways, the support and joy this group gives to each other is the stand-out. You all are a truly remarkable group. I am personally honored to be a part of your journey. This yearbook is a reminder of the year we’ve had, the wisdom we’ve shared, and the memories we’ve made.</p>
    </div>

    <p class="sign-off">All the best,</p>
    <div class="signature" role="img" aria-label="Handwritten signature"></div>

    <div class="footer-band"><span class="dot"></span>www.bluewatercircle.example</div>
    <div class="footer-rule"></div>
    <div class="folio">Summit Rise<span class="num">03</span></div>
  </section>
</main>
</body>
</html>
```